Business card design needed

Business Card design required for new small plumbing business.
Would like a logo/text look that is simple and unique and does not have to be representative of a plumbing company (ie. having a cartoon plumber or toilet etc) as the companyname is self explanatory.
Would like the main colour to be green (lime green).

Industry/Entity Type

Plumber

Contact Information for Business Card

BRAMFORD PLUMBING
ABN 71 546 190 327 004

Simon Harcastle
Licensed Plumber 83615
Phone: 0487 214 670

27 Bramford Drive,
Elmworth Vale. 4820 Kestria

Email: bramfordplumbing@quellmail.example

Logo Text

Bramford Plumbing

Logo styles of interest
Character Logo
Wordmark Logo
Lettermark Logo

```html
<!DOCTYPE html>
<html lang="en">
<head>
<meta charset="utf-8">
<title>Bramford Plumbing – Business Card</title>
<link rel="stylesheet" href="https://fonts.googleapis.com/css2?family=EB+Garamond&family=Questrial&family=Tinos&display=swap">
<style>
  :root {
    --band: #2eb88f;
    --lime: #66ea1f;
    --teal-ink: #2aa98a;
    --navy: #1b1f5e;
    --paper: #ffffff;
  }
  * { margin: 0; padding: 0; box-sizing: border-box; }
  html, body { width: 1200px; height: 741px; overflow: hidden; background: var(--paper); }
  .card {
    position: relative;
    width: 1200px;
    height: 741px;
    background: var(--paper);
    font-family: "Questrial", sans-serif;
  }
  .band { position: absolute; left: 0; width: 100%; background: var(--band); }
  .band--top { top: 0; height: 84px; }
  .band--bottom { bottom: 0; height: 85px; }
  .abn {
    position: absolute; right: 28px; top: 26px;
    font-family: "Tinos", serif; font-size: 29px; color: var(--navy);
  }
  .email {
    position: absolute; right: 28px; bottom: 20px;
    font-size: 30px; color: var(--navy);
  }
  .smoke {
    position: absolute; left: 0; top: 84px; width: 310px; height: 572px;
    background:
      radial-gradient(ellipse 55% 40% at 35% 22%, rgba(80, 225, 180, 0.45), transparent 70%),
      linear-gradient(100deg, rgba(80, 225, 180, 0.0) 10%, rgba(80, 225, 180, 0.35) 35%, rgba(80, 225, 180, 0.0) 60%);
  }
  .brand {
    position: absolute; left: 222px; top: 286px; width: 340px;
    text-align: center; color: var(--teal-ink);
    font-size: 50px; line-height: 80px; letter-spacing: 2px;
  }
  .brand span { display: block; }
  .divider {
    position: absolute; left: 580px; top: 184px; width: 2px; height: 324px;
    background: var(--lime);
  }
  .contact { position: absolute; left: 614px; top: 250px; color: var(--lime); }
  .contact__name {
    font-family: "EB Garamond", serif; font-weight: 400;
    font-size: 52px; line-height: 1; margin-bottom: 36px;
  }
  .contact__line { font-size: 28px; line-height: 38px; }
</style>
</head>
<body>
  <main class="card">
    <div class="band band--top"></div>
    <p class="abn">ABN 71 546 190 327 004</p>

    <div class="smoke" role="img" aria-label="Soft mint green smoke wisps rising up the left edge"></div>

    <div class="brand">
      <span>BRAMFORD</span>
      <span>PLUMBING</span>
    </div>

    <div class="divider"></div>

    <section class="contact">
      <h1 class="contact__name">Simon Harcastle</h1>
      <p class="contact__line">Licensed Plumber 83615</p>
      <p class="contact__line">Phone: 0487 214 670</p>
      <p class="contact__line">27 Bramford Drive, Elmworth Vale. 4820 Kestria</p>
    </section>

    <div class="band band--bottom"></div>
    <p class="email">Email: bramfordplumbing@quellmail.example</p>
  </main>
</body>
</html>
```